Business Landing Page for SEO Company

Need the landing page of the website designed - I will provide the copy, will need to include details of my company and the services offered, about us, testimonials, faq, etc., and all these elements will need to be arranged graphically on the page.

I want something similar to this: https://torvanequill.com/

Not in terms of color or theme or anything, but we offer a similar service and want to display similar information.

Th services we provide are:

Premium Links
Monthly Links Subscription
Link Insertions

Need to advertise them on the front page. Additionally need a place for testimonials, company details, etc.,

We already have logo for the website. Please use the attached file to insert the logo within the overal design.

Target Market(s)

SEO marketers and agencies

Number of Pages Required

1 page

```html
<!DOCTYPE html>
<html lang="en">
<head>
<meta charset="utf-8">
<title>Lumvora – Link Building Agency</title>
<link href="https://fonts.googleapis.com/css2?family=Poppins:wght@400;500;600;700&display=swap" rel="stylesheet">
<style>
:root{
  --blue:#2f8ae6;
  --blue-dark:#1f6fc4;
  --blue-soft:#cfe5fb;
  --blue-pale:#e8f2fd;
  --orange:#ff7a00;
  --ink:#1e1e1e;
  --muted:#555;
  --stage:#ffffff;
  --gray-bg:#f8f9fb;
  --white:#fff;
}
*{margin:0;padding:0;box-sizing:border-box}
html,body{width:1200px;height:3000px;overflow:hidden;background:var(--stage);font-family:'Poppins',sans-serif;color:var(--ink)}
.page{position:absolute;left:272px;top:78px;width:1440px;height:6259px;background:var(--white);transform:scale(.4542);transform-origin:0 0;box-shadow:0 20px 120px rgba(0,0,0,.18);overflow:hidden}
.abs{position:absolute}
.logo{font-weight:600;color:var(--blue);font-size:44px;letter-spacing:-.5px;display:flex;align-items:center;gap:6px}
.logo .dot{width:10px;height:10px;background:var(--orange)}
.nav a{position:absolute;top:36px;font-size:13px;font-weight:500;color:var(--ink);text-decoration:none;text-transform:uppercase}
.btn{position:absolute;background:var(--orange);color:var(--white);border-radius:30px;font-size:15px;font-weight:500;display:flex;align-items:center;justify-content:center;gap:10px}
.card{position:absolute;background:var(--white);border-radius:36px;box-shadow:0 6px 26px rgba(0,0,0,.10);text-align:center}
.card h3{font-size:20px;font-weight:500;margin-bottom:12px}
.card p{font-size:13.5px;line-height:24px;color:var(--muted);padding:0 36px}
.card .more{font-size:14px;color:var(--blue);margin-top:20px;display:block}
.ic{position:absolute;left:50%;transform:translateX(-50%);border-radius:50%;background:var(--orange);display:flex;align-items:center;justify-content:center}
.h2{font-weight:600;color:var(--blue);font-size:36px}
.rule{position:absolute;height:5px;background:var(--orange)}
.para{font-size:14.5px;line-height:29px;color:var(--muted)}
.band{position:absolute;left:0;width:1440px;background:var(--blue);color:var(--white)}
.feat{position:absolute;width:169px;height:169px;border:3px dashed #333;border-radius:50%;display:flex;align-items:center;justify-content:center}
.flabel{position:absolute;width:240px;text-align:center;font-size:17px;font-weight:500}
.client{position:absolute;top:78px;font-size:18px;font-weight:600;color:var(--white);transform:translateX(-50%);white-space:nowrap}
.tcard{position:absolute;top:4081px;width:364px;height:326px;background:var(--white);box-shadow:0 4px 22px rgba(0,0,0,.08);text-align:center}
.tcard .av{position:absolute;left:38px;top:-24px;width:82px;height:82px;border-radius:50%;background:linear-gradient(#c9d2dc,#8d99a6)}
.tcard .q{position:absolute;right:40px;top:8px;font-size:70px;color:#ccc;font-weight:700;line-height:1}
.tcard p{position:absolute;top:90px;left:34px;right:34px;font-size:15px;line-height:33px;color:var(--ink)}
.tcard .line{position:absolute;left:60px;right:60px;top:262px;border-top:1px solid #e5e5e5}
.tcard .stars{position:absolute;top:266px;width:100%;color:var(--orange);font-size:15px;letter-spacing:4px}
.tcard .name{position:absolute;top:292px;width:100%;font-size:15px;color:var(--blue);font-weight:500}
.dots{position:absolute;left:0;width:1440px;display:flex;justify-content:center;gap:14px}
.dots i{width:7px;height:7px;border-radius:50%;background:#bbb}
.dots i:first-child{background:var(--orange)}
.ccard{position:absolute;top:4717px;width:348px;height:346px;background:var(--white);box-shadow:0 4px 22px rgba(0,0,0,.08);text-align:center}
.ccard .art{height:248px;background:linear-gradient(160deg,#eef4fc,#dbe9f8)}
.ccard p{font-size:13px;line-height:28px;padding:18px 28px 0;color:var(--ink)}
.field{position:absolute;background:var(--white);height:42px;font-size:13px;color:#aaa;font-style:italic;padding:12px 18px}
.foot h4{position:absolute;top:5915px;font-size:22px;font-weight:600;color:var(--white)}
.foot .t{position:absolute;font-size:14.5px;color:var(--white);line-height:38px}
.foot .date{font-size:12px;color:#ffc38a;display:flex;align-items:center;gap:6px;line-height:20px}
.foot .date b{width:10px;height:10px;background:var(--orange)}
</style>
</head>
<body>
<div class="page">

  <!-- hero decoration -->
  <svg class="abs" style="left:0;top:0" width="1440" height="900" viewBox="0 0 1440 900">
    <path d="M1010 0 H1440 V640 C1320 700 1150 690 900 610 C760 565 655 470 670 340 C688 200 820 170 900 110 C960 65 990 40 1010 0Z" fill="var(--blue-soft)"/>
    <path d="M0 590 C60 560 100 610 100 700 C100 740 90 770 70 780 H0Z" fill="var(--blue-soft)"/>
  </svg>
  <div class="abs" role="img" aria-label="Illustration of a team building links around a laptop and dashboard" style="left:806px;top:154px;width:556px;height:418px;border-radius:30px;background:linear-gradient(150deg,#bcd9f7,#eaf3fd 60%,#ffe3c8)"></div>

  <!-- header -->
  <div class="abs logo" style="left:77px;top:18px"><span class="dot"></span>Lumvora</div>
  <nav class="nav">
    <a style="left:300px">Guest Post</a>
    <a style="left:420px">Niche Edits</a>
    <a style="left:540px">Tiered Links</a>
    <a style="left:663px">Backlink Packages</a>
    <a style="left:842px">The Link Report</a>
  </nav>

  <!-- hero -->
  <div class="abs" style="left:79px;top:214px;font-size:26px;font-weight:500;color:var(--orange)">Grow your Business with</div>
  <div class="abs" style="left:79px;top:258px;font-size:52px;font-weight:700;color:var(--blue)">Boost Sale With Lumvora</div>
  <p class="abs" style="left:79px;top:340px;width:500px;font-size:14.5px;line-height:26px">Lorem ipsum dolor sit amet, consectetur adipiscing elit. Erat justo in aliquam, adipiscing nam nulla suspendisse molestie.</p>
  <div class="btn" style="left:79px;top:424px;width:236px;height:52px;font-size:14px">Get Free Consulation</div>

  <!-- services -->
  <div class="card" style="left:97px;top:776px;width:359px;height:377px">
    <div class="ic" style="top:22px;width:92px;height:92px"><svg width="40" height="40" viewBox="0 0 24 24" fill="none" stroke="#fff" stroke-width="2" stroke-linecap="round"><path d="M10 14a4 4 0 0 0 6 0l3-3a4 4 0 0 0-6-6l-1 1"/><path d="M14 10a4 4 0 0 0-6 0l-3 3a4 4 0 0 0 6 6l1-1"/></svg></div>
    <div style="padding-top:140px"><h3>Premium Links</h3><p>Lorem ipsum dolor sit amet, consectetur adipiscing elit. Arcu imperdiet quam a sit sapien ullamcorper lectus nullam mauris. Lacinia quis feugiat vestibulum, arcu accumsan metus non.</p><span class="more">Read More ⟶</span></div>
  </div>
  <div class="card" style="left:540px;top:776px;width:359px;height:377px">
    <div class="ic" style="top:22px;width:92px;height:92px"><svg width="40" height="40" viewBox="0 0 24 24" fill="none" stroke="#fff" stroke-width="2"><rect x="4" y="4" width="16" height="16" rx="2"/><path d="M4 10h16M4 15h16M10 4v16M15 4v16"/></svg></div>
    <div style="padding-top:140px"><h3>Monthly Links Subscription</h3><p>Lorem ipsum dolor sit amet, consectetur adipiscing elit. Arcu imperdiet quam a sit sapien ullamcorper lectus nullam mauris. Lacinia quis feugiat vestibulum, arcu accumsan metus non.</p><span class="more">Read More ⟶</span></div>
  </div>
  <div class="card" style="left:983px;top:776px;width:359px;height:377px">
    <div class="ic" style="top:22px;width:92px;height:92px"><svg width="40" height="40" viewBox="0 0 24 24" fill="none" stroke="#fff" stroke-width="2" stroke-linecap="round"><path d="M4 9V4h5M15 4h5v5M20 15v5h-5M9 20H4v-5M12 8v8M8 12h8"/></svg></div>
    <div style="padding-top:140px"><h3>Link Insertions</h3><p>Lorem ipsum dolor sit amet, consectetur adipiscing elit. Arcu imperdiet quam a sit sapien ullamcorper lectus nullam mauris. Lacinia quis feugiat vestibulum, arcu accumsan metus non.</p><span class="more">Read More ⟶</span></div>
  </div>

  <!-- about -->
  <div class="abs h2" style="left:138px;top:1340px">About US</div>
  <div class="rule" style="left:348px;top:1364px;width:246px"></div>
  <p class="abs para" style="left:138px;top:1430px;width:460px">Lorem ipsum dolor sit amet, consectetur adipiscing elit. Et fringilla lacus elit quis leo at varius est elit. Quam volutpat lectus scelerisque enim vel eu sit vitae suspendisse. Cras dui id id mauris feugiat eget. Netus adipiscing ligula vestibulum urna eget id venenatis dis.<br>Quis sodales consectetur netus nec. Malesuada leo, enim gravida sed aliquam. Semper aliquet in facilisis dignissim neque, natoque sem. Arcu faucibus aliquam, malesuada varius ipsum. Morbi tincidunt quam sit elementum amet cras vel ac enim. Tortor tellus eros, volutpat sit habitant sit quis. Netus sem in euismod tincidunt tincidunt. Tristique pellentesque lectus duis orci non purus neque sapien.</p>
  <svg class="abs" style="left:719px;top:1290px" width="602" height="510" viewBox="0 0 602 510"><path d="M60 120 C120 10 260 -10 330 40 C420 100 560 60 560 220 C560 380 440 500 260 490 C110 480 20 380 30 260 C35 200 40 160 60 120Z" fill="var(--blue-soft)"/></svg>
  <div class="abs" role="img" aria-label="Illustration of a laptop with a magnifying glass, gears and a person analysing charts" style="left:790px;top:1360px;width:500px;height:380px;border-radius:24px;background:linear-gradient(140deg,#eaf3fd,#ffffff 45%,#ffd7b0)"></div>

  <!-- band -->
  <div class="band" style="top:1904px;height:210px">
    <div class="abs" style="left:660px;top:18px;width:172px;height:172px;border-radius:50%;border:16px solid rgba(255,255,255,.08)"></div>
    <div class="abs" style="left:233px;top:58px;font-size:22px;font-weight:500">Interested To</div>
    <div class="abs" style="left:233px;top:90px;font-size:34px;font-weight:600">Get Our Fetured Service</div>
    <div class="btn" style="left:1048px;top:86px;width:197px;height:44px;font-size:14px">Get Started ⟶</div>
  </div>

  <!-- features -->
  <div class="card" style="left:97px;top:2301px;width:359px;height:376px">
    <div class="ic" style="top:-90px;width:154px;height:154px"><svg width="62" height="62" viewBox="0 0 24 24" fill="none" stroke="#fff" stroke-width="1.4"><rect x="3" y="4" width="18" height="15" rx="1"/><path d="M3 8h18M7 16v-4M11 16v-6M15 16v-3M19 16v-5"/></svg></div>
    <div style="padding-top:110px"><h3>Quality Over Quantity</h3><p>Lorem ipsum dolor sit amet, consectetur adipiscing elit. Arcu imperdiet quam a sit sapien ullamcorper lectus nullam mauris. Lacinia quis feugiat vestibulum, arcu accumsan metus non.</p><span class="more">Read More ⟶</span></div>
  </div>
  <div class="card" style="left:540px;top:2301px;width:359px;height:376px">
    <div class="ic" style="top:-90px;width:154px;height:154px"><svg width="62" height="62" viewBox="0 0 24 24" fill="none" stroke="#fff" stroke-width="1.6" stroke-linecap="round"><path d="M10 14a4 4 0 0 0 6 0l3-3a4 4 0 0 0-6-6l-1 1"/><path d="M14 10a4 4 0 0 0-6 0l-3 3a4 4 0 0 0 6 6l1-1"/></svg></div>
    <div style="padding-top:110px"><h3>One Off Link Payments</h3><p>Lorem ipsum dolor sit amet, consectetur adipiscing elit. Arcu imperdiet quam a sit sapien ullamcorper lectus nullam mauris. Lacinia quis feugiat vestibulum, arcu accumsan metus non.</p><span class="more">Read More ⟶</span></div>
  </div>
  <div class="card" style="left:983px;top:2301px;width:359px;height:376px">
    <div class="ic" style="top:-90px;width:154px;height:154px"><svg width="62" height="62" viewBox="0 0 24 24" fill="none" stroke="#fff" stroke-width="1.6" stroke-linejoin="round"><path d="M7 11v9H3v-9zM7 11l4-7c1.5 0 2 1 2 2l-1 4h6a2 2 0 0 1 2 2l-2 6a2 2 0 0 1-2 2H7"/></svg></div>
    <div style="padding-top:110px"><h3>Lifetime Link Guarantee</h3><p>Lorem ipsum dolor sit amet, consectetur adipiscing elit. Arcu imperdiet quam a sit sapien ullamcorper lectus nullam mauris. Lacinia quis feugiat vestibulum, arcu accumsan metus non.</p><span class="more">Read More ⟶</span></div>
  </div>

  <!-- experience -->
  <div class="abs" style="left:0;top:2749px;width:1440px;height:910px;background:var(--gray-bg)"></div>
  <div class="abs h2" style="left:0;top:2814px;width:1440px;text-align:center">Our UK Based Agency Has Years Of Experience &amp; Testing</div>
  <div class="abs" style="left:190px;top:2904px;width:1060px;text-align:center;font-size:16px;line-height:33px">
    <p>We’ve been refining our off-page SEO strategy over the past 4 years, figuring out what works and what doesn’t.</p>
    <p style="margin-top:30px">This means that with our link campaigns all you have to do is check that you’re happy with the anchor texts and target URLs we’ve chosen. So, you can focus on other areas of your business, whether that’s lead generation or on-page SEO.</p>
    <p style="margin-top:30px">Based in the United Kingdom (UK), we are continually testing and tweaking to make sure that we are at the forefront of link building techniques.</p>
  </div>
  <svg class="abs" style="left:0;top:3180px" width="1440" height="14"><line x1="200" y1="7" x2="1240" y2="7" stroke="#333" stroke-width="3" stroke-dasharray="8 8"/></svg>
  <div class="feat" style="left:107px;top:3102px;background:var(--gray-bg)"><svg width="70" height="70" viewBox="0 0 24 24" fill="none" stroke="var(--blue)" stroke-width="1.6"><path d="M5 3v18M10 3v18M15 3v18M20 3v18"/><rect x="3" y="8" width="4" height="3" fill="var(--blue)"/><rect x="8" y="13" width="4" height="3" fill="var(--blue)"/><rect x="13" y="6" width="4" height="3" fill="var(--blue)"/><rect x="18" y="15" width="4" height="3" fill="var(--blue)"/></svg></div>
  <div class="feat" style="left:371px;top:3102px;background:var(--gray-bg)"><svg width="70" height="70" viewBox="0 0 24 24" fill="none" stroke="var(--blue)" stroke-width="1.4"><path d="M3 10l9-7 9 7v11H3z"/><path d="M3 10l9 6 9-6M3 21l7-6M21 21l-7-6M12 8v3M12 13v.5"/></svg></div>
  <div class="feat" style="left:635px;top:3102px;background:var(--gray-bg)"><svg width="70" height="70" viewBox="0 0 24 24" fill="none" stroke="var(--blue)" stroke-width="1.4"><circle cx="12" cy="8" r="3"/><circle cx="12" cy="8" r="5" stroke-dasharray="2 2"/><path d="M4 17h5l3 2 6-3 2 1-8 4-8-1"/></svg></div>
  <div class="feat" style="left:899px;top:3102px;background:var(--gray-bg)"><svg width="70" height="70" viewBox="0 0 24 24" fill="none" stroke="var(--blue)" stroke-width="1.4"><rect x="3" y="4" width="18" height="15" rx="1"/><path d="M3 8h18M6 12h12v4H6z"/></svg></div>
  <div class="feat" style="left:1163px;top:3102px;background:var(--gray-bg)"><svg width="70" height="70" viewBox="0 0 24 24" fill="none" stroke="var(--blue)" stroke-width="1.4" stroke-linejoin="round"><path d="M12 3l9 4-9 4-9-4zM3 7v10l9 4 9-4V7M12 11v10"/></svg></div>
  <div class="flabel" style="left:72px;top:3322px">Trusted DR Sorted</div>
  <div class="flabel" style="left:336px;top:3322px">Spam Checked</div>
  <div class="flabel" style="left:600px;top:3322px">British SEO Support</div>
  <div class="flabel" style="left:864px;top:3322px">All Real Sites</div>
  <div class="flabel" style="left:1128px;top:3322px">3-4 Week Delivery</div>
  <div class="btn" style="left:607px;top:3531px;width:220px;height:50px">Get In Touch ⟶</div>

  <!-- clients -->
  <div class="band" style="top:3661px;height:172px">
    <div class="abs" style="left:110px;top:64px;font-size:32px;font-weight:600">Our Clients</div>
    <div class="abs" style="left:376px;top:38px;width:3px;height:96px;background:var(--white)"></div>
    <div class="client" style="left:510px">Market Ledger</div>
    <div class="client" style="left:664px">Rankfold</div>
    <div class="client" style="left:817px">Quillseo</div>
    <div class="client" style="left:971px">Corvid</div>
    <div class="client" style="left:1125px">Tribune Hub</div>
    <div class="client" style="left:1279px">Crawl Weekly</div>
  </div>

  <!-- testimonials -->
  <div class="abs" style="left:0;top:3915px;width:1440px;text-align:center;font-size:15px;text-transform:uppercase">Testimonial</div>
  <div class="abs h2" style="left:0;top:3956px;width:1440px;text-align:center">Happy Clients Say It All</div>
  <div class="tcard" style="left:133px"><div class="av" role="img" aria-label="Client portrait"></div><div class="q">”</div><p>Lorem ipsum dolor sit amet, consectetur adipiscing elit. Neque maecenas egestas morbi sed amet, scelerisque. In eu at sit augue lectus semper ut in.</p><div class="line"></div><div class="stars">★★★★★</div><div class="name">Callum Ashdown</div></div>
  <div class="tcard" style="left:543px"><div class="av" role="img" aria-label="Client portrait"></div><div class="q">”</div><p>Lorem ipsum dolor sit amet, consectetur adipiscing elit. Neque maecenas egestas morbi sed amet, scelerisque. In eu at sit augue lectus semper ut in.</p><div class="line"></div><div class="stars">★★★★★</div><div class="name">Callum Ashdown</div></div>
  <div class="tcard" style="left:953px"><div class="av" role="img" aria-label="Client portrait"></div><div class="q">”</div><p>Lorem ipsum dolor sit amet, consectetur adipiscing elit. Neque maecenas egestas morbi sed amet, scelerisque. In eu at sit augue lectus semper ut in.</p><div class="line"></div><div class="stars">★★★★★</div><div class="name">Callum Ashdown</div></div>
  <div class="dots" style="top:4462px"><i></i><i></i><i></i><i></i></div>

  <!-- case studies -->
  <div class="abs" style="left:0;top:4542px;width:1440px;height:654px;background:var(--gray-bg)"></div>
  <div class="abs" style="left:0;top:4590px;width:1440px;text-align:center;font-size:15px">Latest News</div>
  <div class="abs h2" style="left:0;top:4628px;width:1440px;text-align:center">Our Case Studies</div>
  <div class="ccard" style="left:133px"><div class="art" role="img" aria-label="Illustration of a person saving money in a piggy bank"></div><p>Link Building Budget: How Much Should You Spend on Link Building?</p></div>
  <div class="ccard" style="left:551px"><div class="art" role="img" aria-label="Illustration of a person looking at a globe with location pins"></div><p>Foreign Link Building: Can You Build English Links In Foreign SERPs?</p></div>
  <div class="ccard" style="left:971px"><div class="art" role="img" aria-label="Illustration of a web page with rising ranking markers"></div><p>Link Velocity: Maintain Stronger Rankings Than 90% of SEOs</p></div>
  <div class="dots" style="top:5116px"><i></i><i></i><i></i><i></i></div>

  <!-- questions -->
  <div class="abs h2" style="left:151px;top:5312px">Got Questions?</div>
  <div class="rule" style="left:453px;top:5335px;width:239px"></div>
  <div class="abs" style="left:151px;top:5400px;width:560px;font-size:14.5px;line-height:25px">
    <p>We can provide custom orders suited to your campaign and we’re here to help you in your link building journey. Every step of the way…</p>
    <p style="margin-top:25px">Reach out using the form for any information regarding product selection, bulk discounts, anchor selection or other general enquiries.</p>
    <p style="margin-top:25px">Also, be sure to check out our FAQ’s. These are available on our Category &amp; Product pages. We’re always adding to these and there’s a good chance we’ll have answered your questions within these sections.</p>
  </div>
  <div class="abs" style="left:779px;top:5260px;width:558px;height:461px;background:var(--blue);border-radius:4px">
    <div class="field" style="left:36px;top:40px;width:236px">First Name*</div>
    <div class="field" style="left:286px;top:40px;width:236px">Last Name*</div>
    <div class="field" style="left:36px;top:98px;width:236px">Phone No.*</div>
    <div class="field" style="left:286px;top:98px;width:236px">Email*</div>
    <div class="field" style="left:36px;top:157px;width:486px">Website Url*</div>
    <div class="field" style="left:36px;top:216px;width:486px;height:152px">Any Question*</div>
    <div class="abs" style="left:36px;top:386px;width:486px;height:42px;background:var(--orange);color:var(--white);font-size:14px;display:flex;align-items:center;justify-content:center">Send</div>
  </div>

  <!-- footer -->
  <footer class="foot abs" style="left:0;top:5841px;width:1440px;height:418px;background:linear-gradient(180deg,#3592ea,#1c6fc7)">
  </footer>
  <div class="foot">
    <div class="abs logo" style="left:118px;top:5910px;color:var(--white);font-size:40px"><span class="dot"></span>Lumvora</div>
    <p class="t" style="left:118px;top:5995px;width:384px;line-height:25px">Ready to start a new project or curious about our process? Drop us a note or give us a call. We are happy to answer any questions and provide a free consultation.</p>
    <div class="abs" style="left:118px;top:6115px;display:flex;gap:14px">
      <span style="width:26px;height:26px;background:var(--white)"></span><span style="width:26px;height:26px;background:var(--white)"></span><span style="width:26px;height:26px;background:var(--white)"></span><span style="width:26px;height:26px;background:var(--white)"></span><span style="width:26px;height:26px;background:var(--white)"></span>
    </div>
    <h4 style="left:566px">Navigate</h4>
    <div class="t" style="left:566px;top:5965px">Home<br>About Us<br>Terms &amp; Condition<br>Privacy &amp; Policy<br>FAQ</div>
    <h4 style="left:809px">Recent Aricles</h4>
    <div class="t" style="left:809px;top:5968px;width:260px;line-height:25px">How Much Should You Spend on Link Building?<div class="date"><b></b>Dec 29, 2020</div><div style="margin-top:18px">Maintain Stronger Rankings Than 90% of SEOs</div><div class="date"><b></b>Dec 29, 2020</div></div>
    <h4 style="left:1145px">Contact Us</h4>
    <div class="t" style="left:1145px;top:5965px;line-height:38px">
      <div style="display:flex;align-items:center;gap:16px"><svg width="16" height="16" viewBox="0 0 24 24" fill="#fff"><path d="M6 2l4 4-2 3c1 3 4 6 7 7l3-2 4 4-3 4C10 22 2 14 2 5z"/></svg>555-010-4821</div>
      <div style="display:flex;align-items:center;gap:16px"><svg width="16" height="16" viewBox="0 0 24 24" fill="#fff"><path d="M2 5h20v14H2z"/><path d="M2 5l10 8 10-8" stroke="#2a80dc" stroke-width="2" fill="none"/></svg>hello@lumvora.com</div>
      <div style="display:flex;align-items:center;gap:16px"><svg width="16" height="16" viewBox="0 0 24 24"><circle cx="12" cy="12" r="10" fill="#fff"/><path d="M12 6v6l4 2" stroke="#2a80dc" stroke-width="2" fill="none"/></svg>Mon-Sat, 8AM – 8PM</div>
      <div style="display:flex;gap:16px;line-height:25px;margin-top:4px"><svg width="16" height="16" viewBox="0 0 24 24" fill="#fff" style="margin-top:4px"><path d="M12 2a7 7 0 0 0-7 7c0 5 7 13 7 13s7-8 7-13a7 7 0 0 0-7-7z"/><circle cx="12" cy="9" r="2.5" fill="#2a80dc"/></svg>18 Harbor Lane #2,<br>Westbrook, MA 01990</div>
    </div>
    <div class="abs" style="left:0;top:6220px;width:1440px;height:39px;background:#145db0;color:var(--white);font-size:12px;display:flex;align-items:center;justify-content:center">Copyright 2021 - Lumvora. All right reserved</div>
  </div>

</div>
</body>
</html>
```